Professional, modern and unique business card. We are looking to present a new look to our business cards however we don't want to divert too far away from original template. We want social media links and our 3 office addresses on the backside of the business cards. Please see attached business card templates for ideas.
Crestline Homes Color Code:
R: 7
G:63
B:86

Target Market(s)

Real Estate

Industry/Entity Type

Real Estate

Contact Information for Business Card

Follow the attached templates. In need of a more modern and unique touch but don't want to divert from the original theme or color.
Crestline Homes Color Code:
R: 7
G:63
B:86

Font styles to use
Serif

Requirements
Must have
• Crestline Homes logo, Crestline homes colors, social media links, 3 office addresses,
Nice to have
• information about Crestline Homes and QR codes. You can check out www.mycrestlinehomes.example

```html
<!DOCTYPE html>
<html lang="en">
<head>
<meta charset="utf-8">
<title>Crestline Homes Business Card</title>
<link rel="stylesheet" href="https://fonts.googleapis.com/css2?family=Lato:wght@400;700&display=swap">
<style>
  :root {
    --backdrop: #6e4a2c;
    --card-blue: #137bb5;
    --ink-white: #ffffff;
    --ink-soft: #dde6ee;
    --rule: rgba(255,255,255,0.85);
    --rule-faint: rgba(255,255,255,0.35);
    --icon-fill: #ffffff;
  }
  * { margin: 0; padding: 0; box-sizing: border-box; }
  html, body { width: 1200px; height: 900px; overflow: hidden; }
  body {
    background: var(--backdrop);
    position: relative;
    font-family: "Lato", sans-serif;
    color: var(--ink-white);
  }
  .card {
    position: absolute;
    background: var(--card-blue);
    box-shadow: 3px 4px 6px rgba(0,0,0,0.45);
  }
  .card-front { left: 330px; top: 90px; width: 555px; height: 343px; }
  .card-back  { left: 330px; top: 470px; width: 559px; height: 342px; }

  .front-identity {
    position: absolute; left: 0; right: 0; top: 92px;
    text-align: center; padding-right: 2px;
  }
  .person-name { font-weight: 700; font-size: 20px; line-height: 24px; letter-spacing: 0.2px; }
  .person-title { font-size: 16px; line-height: 20px; }
  .identity-rule {
    width: 196px; height: 1px; background: var(--rule);
    margin: 11px auto 12px;
  }
  .contact-list { list-style: none; font-size: 16px; line-height: 20.3px; }
  .contact-list b { font-weight: 700; }

  .brand-mark {
    position: absolute; left: 40px; top: 116px; width: 222px;
    text-align: center; color: var(--ink-soft);
    font-weight: 700; font-size: 30px; line-height: 36px; letter-spacing: 1px;
    text-transform: uppercase;
  }
  .brand-divider {
    position: absolute; left: 279px; top: 100px; width: 1px; height: 143px;
    background: var(--rule-faint);
  }
  .social-list {
    position: absolute; left: 298px; top: 97px; list-style: none;
  }
  .social-item {
    display: flex; align-items: center; height: 30.6px;
    font-size: 16px;
  }
  .social-dot {
    width: 25px; height: 25px; border-radius: 50%;
    background: var(--icon-fill); margin-right: 6px; flex: none;
  }
  .office-row {
    position: absolute; left: 12px; right: 12px; top: 281px;
    display: flex; justify-content: space-between; align-items: stretch;
    color: var(--ink-soft); font-size: 16px; line-height: 19.5px; text-align: center;
  }
  .office { padding: 0 8px; white-space: nowrap; }
  .office + .office { border-left: 1px solid var(--rule-faint); }
</style>
</head>
<body>

<section class="card card-front" aria-label="Business card front">
  <div class="front-identity">
    <p class="person-name">DANIEL WHITFORD</p>
    <p class="person-title">Managing Director</p>
    <div class="identity-rule"></div>
    <ul class="contact-list">
      <li><b>P:</b> 044-555 010 203</li>
      <li><b>M:</b> 044-555 010 203</li>
      <li><b>F:</b> 044-555 010 203</li>
      <li><b>E:</b> info@crestlinehomes.example</li>
      <li><b>W:</b> www.mycrestlinehomes.example</li>
    </ul>
  </div>
</section>

<section class="card card-back" aria-label="Business card back">
  <p class="brand-mark">Crestline<br>Homes</p>
  <div class="brand-divider"></div>
  <ul class="social-list">
    <li class="social-item"><span class="social-dot"></span>CrestlinehomesNY</li>
    <li class="social-item"><span class="social-dot"></span>Info at Crestline Homes</li>
    <li class="social-item"><span class="social-dot"></span>Crestline Homes New York</li>
    <li class="social-item"><span class="social-dot"></span>Crestline Homes</li>
    <li class="social-item"><span class="social-dot"></span>@CrestlineHomesQ</li>
  </ul>
  <div class="office-row">
    <p class="office">412-07 Harbor Blvd<br>Bayside Point, NY 11360</p>
    <p class="office">73-40 Maple Blvd<br>Kew Hollow, NY 11418</p>
    <p class="office">2250 Orchard Ave<br>Eastbrook, NY 11207</p>
  </div>
</section>

</body>
</html>
```